Velvet Lantern rebranding my business with a new business card

I have my new logo and now I need a refresher on my business cards. I really want something fun and fresh. I like black background or anything to make the color pop.
Logo
Name: Velvet Lantern
Contact Info as stated below:
Mira Pellow
555-013-4762
Logo
Name: Velvet Lantern
Mira Pellow
555-013-4762
fb.me/VelvetLanternbyMira
Instagram: @VelvetLanternbyMira

Industry/Entity Type

Business

Contact Information for Business Card

double-sided. Logo on one side. Contact info on the other.

Requirements
Must have
• Logo
• Name: Velvet Lantern
• Contact Info as stated below:
• Mira Pellow
• 555-013-4762
• fb.me/VelvetLanternbyMira
• fb.me/VelvetLanternbyMira

```html
<!DOCTYPE html>
<html lang="en">
<head>
<meta charset="utf-8">
<title>Velvet Lantern – Business Card</title>
<link href="https://fonts.googleapis.com/css2?family=Fenix&display=swap" rel="stylesheet">
<style>
  :root {
    --backdrop: #0e0e0e;
    --card-dark: #1b1b1c;
    --card-light: #2c2c2d;
    --pink: #e389c2;
    --green: #86c67f;
    --cream: #efe6c8;
    --ink: #1b1b1c;
  }
  * { box-sizing: border-box; margin: 0; padding: 0; }
  html, body {
    width: 1200px; height: 1000px; overflow: hidden;
    background: var(--backdrop);
    font-family: "Fenix", Georgia, serif;
  }
  .card-pair {
    position: absolute; top: 350px; left: 60px;
    display: flex; gap: 40px;
  }
  .card {
    position: relative; width: 520px; height: 300px;
    border-radius: 22px; overflow: hidden;
    background: radial-gradient(ellipse at 55% 40%, var(--card-light), var(--card-dark) 75%);
    box-shadow: 0 12px 30px rgba(0,0,0,.6);
  }
  /* Front side */
  .card-front .ring { position: absolute; inset: 0; }
  .brand-mark {
    position: absolute; top: 50%; left: 50%;
    transform: translate(-50%, -50%);
    display: flex; flex-direction: column; align-items: center; gap: 12px;
  }
  .brand-dot { width: 46px; height: 46px; border-radius: 50%; background: var(--pink); }
  .brand-name { color: var(--cream); font-size: 30px; letter-spacing: 1px; }
  /* Back side */
  .holder-name {
    position: absolute; top: 96px; right: 46px;
    color: var(--pink); font-size: 52px; letter-spacing: 1px;
  }
  .contact {
    position: absolute; display: flex; align-items: center; gap: 8px;
    color: var(--cream); font-size: 17px;
  }
  .contact-phone { left: 22px; bottom: 34px; }
  .contact-social { left: 210px; bottom: 34px; }
  .icon-badge {
    width: 24px; height: 24px; border-radius: 50%; background: var(--cream);
    display: flex; align-items: center; justify-content: center;
  }
  .color-band { position: absolute; left: 0; right: 0; bottom: 0; height: 14px; display: flex; }
  .color-band span { flex: 1; }
  .band-green { background: var(--green); }
  .band-pink { background: var(--pink); }
  .band-cream { background: var(--cream); }
</style>
</head>
<body>
  <div class="card-pair">
    <section class="card card-front" aria-label="Card front">
      <svg class="ring" width="520" height="300" viewBox="0 0 520 300">
        <circle cx="260" cy="150" r="165" fill="none" stroke="var(--pink)" stroke-width="5"/>
        <circle cx="260" cy="150" r="152" fill="none" stroke="var(--pink)" stroke-width="3"/>
      </svg>
      <div class="brand-mark">
        <div class="brand-dot"></div>
        <div class="brand-name">Velvet Lantern</div>
      </div>
    </section>

    <section class="card card-back" aria-label="Card back">
      <h1 class="holder-name">Mira Pellow</h1>
      <div class="contact contact-phone">
        <span class="icon-badge">
          <svg width="14" height="14" viewBox="0 0 24 24"><path fill="var(--ink)" d="M6.6 10.8a15.1 15.1 0 0 0 6.6 6.6l2.2-2.2a1 1 0 0 1 1-.25 11.4 11.4 0 0 0 3.6.57 1 1 0 0 1 1 1V20a1 1 0 0 1-1 1A17 17 0 0 1 3 4a1 1 0 0 1 1-1h3.5a1 1 0 0 1 1 1 11.4 11.4 0 0 0 .57 3.6 1 1 0 0 1-.25 1z"/></svg>
        </span>
        <span>555-013-4762</span>
      </div>
      <div class="contact contact-social">
        <span class="icon-badge"></span>
        <span>VelvetLanternbyMira</span>
      </div>
      <div class="color-band">
        <span class="band-green"></span>
        <span class="band-pink"></span>
        <span class="band-cream"></span>
      </div>
    </section>
  </div>
</body>
</html>
```